Toriva Letterhead

Hi Kelvara:

I would like a card that is cleanly laid out, with adequate white space for the text to breathe. We don't need a fax number.
The address is:
4120 Marlow Crest Drive, Suite 210
Plano Texas 75081

Gordon R. Whitfield
Managing Director
469.517.3846 (d)
214.639.4705 (m)
gwhitfield@torivafunds.example

The Kanji characters for Toriva are: 朝凪
It would be good if you could fit the kanji in as well.

Thank you, Gordon

```html
<!DOCTYPE html>
<html lang="en">
<head>
<meta charset="UTF-8">
<title>Toriva Letterhead</title>
<link rel="stylesheet" href="https://fonts.googleapis.com/css2?family=Cinzel:wght@400&family=Josefin+Sans:wght@400;600&family=Noto+Serif+JP:wght@300&display=swap">
<style>
  :root {
    --navy: #1e3a66;
    --slate: #8a8f96;
    --ink: #222428;
    --rule: #b9bcc1;
    --paper: #ffffff;
  }
  html, body {
    margin: 0;
    padding: 0;
    width: 849px;
    height: 1200px;
    overflow: hidden;
    background: var(--paper);
  }
  .letterhead {
    position: relative;
    width: 849px;
    height: 1200px;
    box-sizing: border-box;
    border: 1.5px solid var(--rule);
    background: var(--paper);
  }
  .brand {
    position: absolute;
    left: 52px;
    top: 64px;
    display: flex;
    align-items: flex-start;
  }
  .brand-square {
    width: 64px;
    height: 64px;
    background: var(--navy);
    margin-top: 12px;
  }
  .brand-divider {
    width: 1.5px;
    height: 92px;
    background: var(--rule);
    margin: 0 16px 0 22px;
  }
  .brand-text {
    display: flex;
    flex-direction: column;
  }
  .brand-name {
    font-family: "Cinzel", serif;
    font-weight: 400;
    font-size: 36px;
    letter-spacing: 0.5px;
    color: var(--navy);
    line-height: 1;
    margin-top: 14px;
  }
  .brand-kanji {
    font-family: "Noto Serif JP", serif;
    font-weight: 300;
    font-size: 34px;
    color: var(--slate);
    line-height: 1;
    margin-top: 8px;
  }
  .contact {
    position: absolute;
    left: 574px;
    top: 72px;
    font-family: "Josefin Sans", sans-serif;
    color: var(--ink);
    font-size: 15px;
    line-height: 22px;
  }
  .contact p { margin: 0; }
  .contact .web {
    font-weight: 600;
    margin-top: 10px;
  }
</style>
</head>
<body>
  <main class="letterhead">
    <header class="brand">
      <div class="brand-square" aria-hidden="true"></div>
      <div class="brand-divider" aria-hidden="true"></div>
      <div class="brand-text">
        <span class="brand-name">Toriva Capital</span>
        <span class="brand-kanji" lang="ja">朝凪</span>
      </div>
    </header>
    <address class="contact">
      <p>4120 Marlow Crest Drive,</p>
      <p>Suite 210, Plano Texas 75081</p>
      <p class="web">www.torivacapital.example</p>
    </address>
  </main>
</body>
</html>
```